A new updated business card. A good first impression for new customers to our business.

I need something unique. I will attached a picture of our old rubbish cards, and also our current Logo ( I think this needs an update if you have any ideas, its very basic and budget)The best way you will get to see my business is checking our Facebook page, I don't really know what else to say, but anything you want to know, ask away.www.facebook.com/tkwashandseal/

Target Market(s)

Home owners

Industry/Entity Type

Business

Contact Information for Business Card

T&K's Pressure Cleaning & Concrete Sealing
Maya 0492 615 370 maya@tkwashandseal.com
Dylan 0431 528 906 dylan@tkwashandseal.com

FB: www.facebook.com/tkwashandseal/
Website: www.tkwashandseal.net (This is pretty rubbish- we don't really use it)

100% customer satisfaction guaranteed

All aspects of Hi-Pressure Cleaning
Sealing & Re-Sealing
Roof Cleaning
Colour sealing
Decorative coatings

Free no obligation quotes

Requirements
Must have
• NO OBLIGATION FREE quotes
• 100% Customer satisfaction guaranteed
• Can you please add both names, contact details and email address on one card.
• Dylan 0431 528 906
• dylan@tkwashandseal.com
• Maya 0492 615 370
• maya@tkwashandseal.com
• Please change the services:
• Hot/Cold Hi-Pressure Cleaning
• Sealing & Re-Sealing
• Roof Cleaning
• Colour Sealing
• Decorative Coatings
• Concrete Honing
• Thanks
Nice to have
• Something a bit different, something eye catching.l

```html
<!DOCTYPE html>
<html lang="en">
<head>
<meta charset="utf-8">
<title>T&amp;K's Pressure Cleaning &amp; Concrete Sealing – Business Card</title>
<link rel="stylesheet" href="https://fonts.googleapis.com/css2?family=Anton&family=Open+Sans:wght@400;600;700;800&display=swap">
<style>
  :root {
    --bg: #e9e6e1;
    --card-dark: #2b2b2b;
    --card-dark-line: #323232;
    --card-light: #ffffff;
    --red: #e3202a;
    --grey-band: #55575a;
    --ink: #2a2a2a;
    --white: #ffffff;
  }
  * { box-sizing: border-box; margin: 0; padding: 0; }
  html, body {
    width: 1200px; height: 900px; overflow: hidden;
    background: var(--bg);
    font-family: "Open Sans", Arial, sans-serif;
  }
  .card {
    position: absolute;
    left: 270px;
    width: 660px; height: 403px;
    border-radius: 4px;
    box-shadow: 0 6px 18px rgba(0,0,0,.18);
    overflow: hidden;
  }

  /* ---------- Back: services ---------- */
  .card-back {
    top: 36px;
    background:
      repeating-linear-gradient(0deg, var(--card-dark) 0 3px, var(--card-dark-line) 3px 4px);
    color: var(--white);
    padding: 40px 44px 0 56px;
  }
  .services-title {
    font-family: "Anton", Impact, sans-serif;
    font-weight: 400;
    font-size: 40px;
    line-height: 1.02;
    letter-spacing: 1px;
    text-align: center;
    text-transform: uppercase;
    margin-left: 30px;
  }
  .guarantee {
    font-weight: 800;
    font-size: 22.5px;
    margin-top: 14px;
    white-space: nowrap;
  }
  .service-list {
    list-style: none;
    display: flex; flex-wrap: wrap;
    column-gap: 22px; row-gap: 6px;
    margin-top: 16px;
    font-size: 16.5px;
    width: 560px;
  }
  .service-list li {
    position: relative;
    padding-left: 18px;
    white-space: nowrap;
  }
  .service-list li::before {
    content: "";
    position: absolute; left: 0; top: 8px;
    width: 8px; height: 8px; border-radius: 50%;
    background: var(--red);
  }
  .service-list .row-break { flex-basis: 100%; height: 0; padding: 0; }
  .service-list .row-break::before { display: none; }
  .free-quotes {
    display: inline-block;
    margin-top: 20px;
    padding: 6px 16px;
    background: var(--red);
    color: var(--white);
    font-weight: 800;
    font-size: 17px;
    letter-spacing: .8px;
    text-transform: uppercase;
    white-space: nowrap;
  }

  /* ---------- Front: contacts ---------- */
  .card-front {
    top: 466px;
    background: var(--card-light);
    color: var(--ink);
  }
  .front-bands { position: absolute; inset: 0; }
  .contacts {
    position: absolute; left: 46px; top: 36px;
    font-size: 16px;
    line-height: 1.5;
  }
  .contact-name {
    color: var(--red);
    font-weight: 700;
    font-size: 19px;
    line-height: 1.3;
    margin-left: 18px;
  }
  .contact-person + .contact-person { margin-top: 6px; }
  .contact-line { display: flex; align-items: center; gap: 12px; }
  .contact-line svg { width: 14px; height: 14px; flex: none; }
  .social { margin-top: 6px; }
  .dot-mark {
    width: 12px; height: 12px; border-radius: 50%;
    background: var(--red); flex: none; margin: 0 1px;
  }

  .brand {
    position: absolute; right: 40px; top: 150px;
    display: flex; align-items: center; gap: 12px;
  }
  .brand-dot {
    width: 20px; height: 20px; border-radius: 50%;
    background: var(--red); flex: none;
  }
  .brand-name {
    font-weight: 700;
    font-size: 18px;
    line-height: 1.2;
    color: var(--ink);
    text-transform: uppercase;
    letter-spacing: .5px;
  }
</style>
</head>
<body>

<section class="card card-back" aria-label="Services">
  <h1 class="services-title">Pressure Cleaning<br>&amp; Concrete Sealing</h1>
  <p class="guarantee">100% customer satisfaction guaranteed</p>
  <ul class="service-list">
    <li>Hot/Cold Hi-Pressure Cleaning</li>
    <li>Sealing &amp; Re-Sealing</li>
    <li class="row-break" aria-hidden="true"></li>
    <li>Roof Cleaning</li>
    <li>Colour Sealing</li>
    <li>Decorative Coatings</li>
    <li class="row-break" aria-hidden="true"></li>
    <li>Concrete Honing</li>
  </ul>
  <p class="free-quotes">No obligation free quotes</p>
</section>

<section class="card card-front" aria-label="Contacts">
  <svg class="front-bands" viewBox="0 0 660 403" aria-hidden="true">
    <polygon points="0,322 300,322 288,340 0,340" fill="var(--grey-band)"/>
    <polygon points="312,346 660,346 660,403 290,403" fill="var(--red)"/>
  </svg>

  <div class="contacts">
    <div class="contact-person">
      <p class="contact-name">Maya</p>
      <p class="contact-line">
        <svg viewBox="0 0 24 24"><path fill="var(--red)" d="M6.6 10.8a15.1 15.1 0 0 0 6.6 6.6l2.2-2.2a1 1 0 0 1 1-.25 11.4 11.4 0 0 0 3.6.57 1 1 0 0 1 1 1V20a1 1 0 0 1-1 1A17 17 0 0 1 3 4a1 1 0 0 1 1-1h3.5a1 1 0 0 1 1 1c0 1.250.2 2.45.57 3.57a1 1 0 0 1-.25 1z"/></svg>
        0492 615 370
      </p>
      <p class="contact-line">
        <svg viewBox="0 0 24 24"><path fill="var(--red)" d="M2 5h20v14H2z"/><path fill="none" stroke="#fff" stroke-width="1.8" d="M2.5 5.5 12 13l9.5-7.5"/></svg>
        maya@tkwashandseal.com
      </p>
    </div>
    <div class="contact-person">
      <p class="contact-name">Dylan</p>
      <p class="contact-line">
        <svg viewBox="0 0 24 24"><path fill="var(--red)" d="M6.6 10.8a15.1 15.1 0 0 0 6.6 6.6l2.2-2.2a1 1 0 0 1 1-.25 11.4 11.4 0 0 0 3.6.57 1 1 0 0 1 1 1V20a1 1 0 0 1-1 1A17 17 0 0 1 3 4a1 1 0 0 1 1-1h3.5a1 1 0 0 1 1 1c0 1.25.2 2.45.57 3.57a1 1 0 0 1-.25 1z"/></svg>
        0431 528 906
      </p>
      <p class="contact-line">
        <svg viewBox="0 0 24 24"><path fill="var(--red)" d="M2 5h20v14H2z"/><path fill="none" stroke="#fff" stroke-width="1.8" d="M2.5 5.5 12 13l9.5-7.5"/></svg>
        dylan@tkwashandseal.com
      </p>
    </div>
    <div class="social">
      <p class="contact-line"><span class="dot-mark" aria-hidden="true"></span>tkwashandseal</p>
      <p class="contact-line">
        <svg viewBox="0 0 24 24"><circle cx="12" cy="12" r="10" fill="var(--red)"/><path fill="none" stroke="#fff" stroke-width="1.5" d="M2 12h20M12 2c3 3 3 17 0 20M12 2c-3 3-3 17 0 20"/></svg>
        www.tkwashandseal.net
      </p>
    </div>
  </div>

  <div class="brand">
    <span class="brand-dot" aria-hidden="true"></span>
    <p class="brand-name">T&amp;K's Pressure Cleaning<br>&amp; Concrete Sealing</p>
  </div>
</section>

</body>
</html>
```